Lumen Fitness Personal Training Business

I need a business card design with a logo for my personal training company. I'd like the colors to be a vibrant green and black. I'd like the logo to incorporate an anvil (or something similar). I train hardcore competitive athletes as well as soccer moms trying to get and/or stay in shape. I need a logo that will not pigeon hole me in one category or the other, but at the same time not be too intimidating to soccer moms, but will not be off putting to the more hardcore trainees. The design should be attention grabbing and aesthetic.
Target Market(s)
Hardcore athletes as well as average people just trying to get/stay in shape.
Industry/Entity Type
Training

```html
<!DOCTYPE html>
<html lang="en">
<head>
<meta charset="utf-8">
<title>Lumen Fitness – Business Card</title>
<link rel="stylesheet" href="https://fonts.googleapis.com/css2?family=Montserrat:wght@700;800&family=Open+Sans:wght@400;600&display=swap">
<style>
  :root {
    --brand-green: #1aa84b;
    --ink-black: #111111;
    --paper-white: #ffffff;
    --backdrop: #e9e6e1;
    --card-w: 900px;
    --card-h: 514px;
  }
  * { margin: 0; padding: 0; box-sizing: border-box; }
  html, body {
    width: 1200px;
    height: 1200px;
    overflow: hidden;
    background: var(--backdrop);
  }
  .canvas {
    position: relative;
    width: 1200px;
    height: 1200px;
  }
  .card {
    position: absolute;
    left: 150px;
    width: var(--card-w);
    height: var(--card-h);
    overflow: hidden;
    box-shadow: 0 6px 18px rgba(0,0,0,0.18);
  }
  .card--back {
    top: 56px;
    background: var(--ink-black);
    display: flex;
    align-items: center;
    justify-content: center;
  }
  .card--front {
    top: 630px;
    background: var(--paper-white);
  }

  /* Wordmark */
  .wordmark {
    font-family: "Montserrat", sans-serif;
    font-weight: 800;
    text-transform: uppercase;
    line-height: 0.92;
    letter-spacing: 0.02em;
  }
  .wordmark--back {
    color: var(--paper-white);
    font-size: 92px;
    text-align: center;
  }
  .wordmark--back .mark-square {
    display: block;
    width: 54px;
    height: 54px;
    margin: 0 auto 26px;
    background: var(--paper-white);
  }
  .front-brand {
    position: absolute;
    left: 40px;
    top: 40px;
    display: flex;
    align-items: center;
    gap: 16px;
  }
  .front-brand .mark-square {
    width: 40px;
    height: 40px;
    background: var(--brand-green);
  }
  .wordmark--front {
    color: var(--ink-black);
    font-size: 46px;
  }

  /* Contact block */
  .contact {
    position: absolute;
    left: 40px;
    top: 196px;
    font-family: "Open Sans", sans-serif;
    font-size: 19px;
    line-height: 1.4;
    color: var(--brand-green);
    list-style: none;
  }
  .contact .address { margin-bottom: 14px; }
  .contact .label { color: var(--ink-black); font-weight: 600; }

  /* Person */
  .person {
    position: absolute;
    left: 560px;
    top: 250px;
  }
  .person__name {
    font-family: "Montserrat", sans-serif;
    font-weight: 700;
    font-size: 34px;
    color: var(--ink-black);
  }
  .person__role {
    font-family: "Open Sans", sans-serif;
    font-size: 21px;
    color: var(--brand-green);
    margin-top: 4px;
  }

  /* Bottom bands */
  .bands {
    position: absolute;
    left: 0;
    bottom: 0;
    width: 900px;
    height: 120px;
  }
  .band-green { fill: var(--brand-green); }
  .band-black { fill: var(--ink-black); }
</style>
</head>
<body>
<main class="canvas">

  <section class="card card--back" aria-label="Card back">
    <div class="wordmark wordmark--back">
      <span class="mark-square"></span>
      Lumen<br>Fitness
    </div>
  </section>

  <section class="card card--front" aria-label="Card front">
    <div class="front-brand">
      <span class="mark-square"></span>
      <div class="wordmark wordmark--front">Lumen<br>Fitness</div>
    </div>

    <ul class="contact">
      <li class="address">48 Kestrel Lane<br>Ashford, 204518</li>
      <li><span class="label">p:</span> 055-610 274 318</li>
      <li><span class="label">f:</span> 055-610 274 318</li>
      <li><span class="label">e:</span> info@lumenfit.com</li>
    </ul>

    <div class="person">
      <div class="person__name">Daniel Reyes</div>
      <div class="person__role">Managing Director</div>
    </div>

    <svg class="bands" viewBox="0 0 900 120" aria-hidden="true">
      <polygon class="band-green" points="0,20 430,20 410,44 0,44"/>
      <polygon class="band-black" points="446,20 900,20 900,120 380,120"/>
    </svg>
  </section>

</main>
</body>
</html>
```